Cleaning Service Company In need of Good Web presence.

The company is a cleaning service company which provides professional staff and service for cleaning. This is a project to build a site that is both solid and a strong recognition of our organization. It is supposed to show quality, cleanliness, professionalism. The use of images and art for imagery is all good just to have a site that is consistent and solid. There might be a chance to make stationary, logo and business cars if someone feels they can build a brand that is consistent. The image we are going for is clean solid and to stand out. Finally stationary should not be expensive to print.

Current logo is attached and can be used or can be made more creative.

Target Market(s)

Corporate and Government entities, that will feel that this company has a brand that sets it apart from the rest. The company is new so the modification of the logo will not be an issue if a more solid brand come out of this project. The idea is to have a clean consistent product that stands our from others in terms of website, stationary, etc

Industry/Entity Type

Cleaning Service

Contact Information for Business Card

P.O.Box 51947
Riffa
Kingdom of Bahrain

Logo Text

Harbor Lane Services

Number of Pages Required

4 page

Font styles to use
Sans Serif

Colors
abd036
cadf82
eaf2ce
9bcb3b

Requirements
Must have
• Green Color to be used in order to stick to the name. Also the creativity and boldness in an elegant manner.
Nice to have
• Arabic name of company
• هاربر لين سرفسس ذ.م.م
• if cannot be put at least make a location should be chosen
• Also could be a bit of 3D given to the logo if it could stay elegent.
Should not have
• Should not show people cleaning.

```html
<!DOCTYPE html>
<html lang="en">
<head>
<meta charset="utf-8">
<title>Harbor Lane Services W.L.L</title>
<link href="https://fonts.googleapis.com/css2?family=Roboto+Slab:wght@300;400;700&family=Roboto:wght@300;400;500;700&display=swap" rel="stylesheet">
<style>
:root{
  --green-dark:#0b6b3f;
  --green-deep:#0e5e36;
  --green:#9bcb3b;
  --green-bright:#abd036;
  --green-soft:#cadf82;
  --green-pale:#eaf2ce;
  --ink:#222;
  --grey:#666;
  --paper:#f7f7f5;
  --black:#111;
}
*{box-sizing:border-box;margin:0;padding:0}
html,body{width:1200px;height:2497px;overflow:hidden}
body{position:relative;font-family:'Roboto',sans-serif;color:var(--ink);background:#fff}
.abs{position:absolute}

/* top bar */
.topbar{left:0;top:0;width:1200px;height:27px;background:var(--green-dark);color:#fff;font-size:12px;display:flex;align-items:center;padding:0 161px;justify-content:space-between}
.topbar .contacts{display:flex;gap:18px;align-items:center}
.topbar svg{width:11px;height:11px;vertical-align:-1px;margin-right:4px;fill:#fff}

/* hero */
.hero{left:0;top:27px;width:1200px;height:593px;background:linear-gradient(180deg,#4a6a86 0%,#7e93a6 35%,#a9abab 62%,#d7d6d2 100%)}
.nav{left:0;top:27px;width:1200px;height:85px;background:rgba(155,203,59,.82)}
.brandpanel{left:0;top:27px;width:355px;height:85px;background:#f2f6ea;clip-path:polygon(0 0,100% 0,87% 100%,0 100%)}
.brand{left:160px;top:37px;display:flex;align-items:center;gap:10px}
.brand .dot{width:64px;height:64px;border-radius:50%;background:var(--green)}
.brand span{font-family:'Roboto Slab',serif;font-weight:700;font-size:13px;color:var(--green-dark);line-height:1.15;width:110px}
.menu{left:374px;top:27px;height:85px;display:flex;align-items:center;color:#fff;font-size:13px}
.menu a{color:#fff;text-decoration:none;padding:0 25px}
.hero-text{left:0;top:290px;width:1200px;text-align:center;color:#fff}
.hero-text .kicker{font-family:'Roboto Slab',serif;font-weight:300;font-size:32px;letter-spacing:.5px}
.hero-text h1{font-family:'Roboto Slab',serif;font-weight:700;font-size:45px;margin-top:2px;letter-spacing:.5px}
.hero-text p{font-size:16px;margin-top:6px}
.btn-call{left:538px;top:436px;width:122px;height:36px;border-radius:18px;background:var(--green);border:2px solid #e8f3c9;color:var(--green-deep);font-size:14px;display:flex;align-items:center;justify-content:center;gap:6px}
.arrow{width:40px;height:40px;border-radius:50%;background:rgba(255,255,255,.6);display:flex;align-items:center;justify-content:center}
.arrow svg{width:22px;height:22px;fill:#555}

/* welcome */
.welcome{left:0;top:620px;width:1200px;height:432px;background:var(--paper);border-top:3px solid var(--green-pale)}
.heading{font-family:'Roboto Slab',serif;font-weight:700;font-size:30px;color:var(--black);letter-spacing:-.5px}
.subhead{font-size:12px;letter-spacing:3px;color:var(--grey)}
.body-copy{font-size:11px;line-height:15px;color:var(--grey)}
.btn-outline{width:114px;height:36px;border:2px solid var(--green-dark);border-radius:18px;color:var(--green-dark);font-size:15px;display:flex;align-items:center;justify-content:center;background:#fff}
.why{left:775px;top:696px;width:282px;height:46px;background:var(--green-bright);border-right:5px solid var(--green-dark);font-family:'Roboto Slab',serif;font-weight:700;font-size:26px;color:var(--black);display:flex;align-items:center;justify-content:center}
.bubble{border-radius:50%;color:#fff;text-align:center;display:flex;flex-direction:column;align-items:center;justify-content:center;padding:0 30px}
.bubble h3{font-family:'Roboto Slab',serif;font-size:16px;font-weight:700;margin:6px 0 4px;letter-spacing:.5px}
.bubble p{font-size:10px;line-height:13px}
.bubble b{font-family:'Roboto Slab',serif;font-size:13px;margin-top:8px}
.bubble svg{width:36px;height:36px;fill:none;stroke:#fff;stroke-width:2}
.b-green{background:var(--green);border:4px solid #d6ea9c}
.b-dark{background:var(--green-deep);border:4px solid var(--green)}

/* services */
.services{left:0;top:1052px;width:1200px;height:588px;background:radial-gradient(circle at 30% 60%,#c2dc6b,#a9cd3d 70%)}
.services-title{left:0;top:1105px;width:1200px;text-align:center}
.services-title h2{font-family:'Roboto Slab',serif;font-weight:700;font-size:38px;color:#1d2b10}
.services-title p{font-size:16px;color:#1d2b10;margin-top:2px}
.rule{height:2px;background:#fff;width:44px}
.card{width:277px;height:405px;top:1210px}
.card .photo{height:185px;border:3px solid #fff;border-bottom:none}
.card .panel{height:220px;text-align:center;padding:30px 16px 0}
.card h3{font-family:'Roboto Slab',serif;font-weight:400;font-size:19px;letter-spacing:.5px}
.card p{font-size:11px;line-height:15px;margin-top:14px}
.card .more{margin:18px auto 0;width:124px;height:36px;border-radius:18px;font-size:14px;display:flex;align-items:center;justify-content:center;gap:6px}
.card.dark .panel{background:var(--green-deep);color:#fff}
.card.dark .more{background:var(--green);border:2px solid #d4ea95;color:#fff}
.card.light .panel{background:var(--green-soft);color:#1d2b10}
.card.light .more{background:var(--green-deep);border:2px solid #fff;color:#fff}

/* how it works */
.how{left:0;top:1640px;width:1200px;height:256px;background:var(--paper);border-bottom:3px solid var(--green-bright)}
.step{width:150px;text-align:center;top:1697px}
.step .ring{width:66px;height:66px;margin:0 auto;border-radius:50%;border:3px solid #cfe3a1;background:#fff;display:flex;align-items:center;justify-content:center}
.step svg{width:36px;height:36px;fill:none;stroke:var(--green-deep);stroke-width:2}
.step p{font-family:'Roboto Slab',serif;font-weight:300;font-size:17px;line-height:19px;margin-top:16px;color:#333}
.step p em{font-style:normal;color:var(--green)}

/* contact strip */
.strip{left:0;top:1896px;width:1200px;height:114px;background:#fff}
.info{top:1930px;display:flex;gap:14px;align-items:flex-start}
.info svg{width:52px;height:48px;fill:none;stroke:var(--green);stroke-width:2}
.info h4{font-size:12px;font-weight:500;color:var(--green-dark);letter-spacing:.5px}
.info p{font-size:14px;color:#333;margin-top:4px}
.info p.small{font-size:11px;line-height:14px;width:230px}

/* contact form + map */
.contact{left:0;top:2010px;width:600px;height:433px;background:linear-gradient(135deg,#3a3a3a,#1f1f1f 60%,#2c2c2c)}
.map{left:600px;top:2010px;width:600px;height:433px;background:linear-gradient(160deg,#b7d6c4 0%,#cfe2b0 40%,#e6ebb8 60%,#b8d8c8 100%)}
.contact-title{left:158px;top:2036px;font-family:'Roboto Slab',serif;font-weight:300;font-size:33px;color:var(--green-bright);letter-spacing:1px}
.field{left:158px;width:420px;height:34px;border:1px solid #555;background:rgba(0,0,0,.25);color:#999;font-size:11px;padding:0 12px;display:flex;align-items:center}
.field.message{height:123px;align-items:flex-start;padding-top:10px}
.submit{left:161px;top:2386px;width:92px;height:32px;background:var(--green);border:1px solid #cfe59a;color:#fff;font-size:15px;display:flex;align-items:center;justify-content:center;gap:6px}

/* footer */
.foot-left{left:0;top:2443px;width:600px;height:54px;background:var(--green-dark);color:#fff;font-size:11px;padding-left:158px;display:flex;align-items:center}
.foot-right{left:600px;top:2443px;width:600px;height:54px;background:var(--black);color:#ddd;font-size:14px;display:flex;align-items:center;justify-content:flex-end;padding-right:158px;gap:10px}
.social{width:24px;height:24px;border-radius:50%;border:2px solid var(--green)}
</style>
</head>
<body>

<div class="abs topbar">
  <span>Harbor Lane Services W.L.L</span>
  <div class="contacts">
    <span><svg viewBox="0 0 24 24"><path d="M6.6 10.8a15 15 0 006.6 6.6l2.2-2.2a1 1 0 011-.25 11.4 11.4 0 003.6.57 1 1 0 011 1V20a1 1 0 01-1 1A17 17 0 013 4a1 1 0 011-1h3.5a1 1 0 011 1c0 1.25.2 2.45.57 3.6a1 1 0 01-.25 1z"/></svg>(000) 000-0000</span>
    <span><svg viewBox="0 0 24 24"><path d="M2 5h20v14H2z M2 5l10 8 10-8" stroke="#fff" stroke-width="2" fill="none"/></svg>info@harborlaneservices.com</span>
    <span><svg viewBox="0 0 24 24"><path d="M12 2a7 7 0 00-7 7c0 5 7 13 7 13s7-8 7-13a7 7 0 00-7-7zm0 9.5A2.5 2.5 0 1112 6.5a2.5 2.5 0 010 5z"/></svg>Find us on map</span>
  </div>
</div>

<div class="abs hero" role="img" aria-label="Photo of a polished marble floor in a bright office with a floor machine and city view through tall windows"></div>
<div class="abs nav"></div>
<div class="abs brandpanel"></div>
<div class="abs brand"><div class="dot"></div><span>Harbor Lane Services</span></div>
<nav class="abs menu">
  <a>Home</a><a>About Us</a><a>Service</a><a>Quotes</a><a>Testimonials</a><a>Payments</a><a>Contact Us</a>
</nav>
<div class="abs arrow" style="left:27px;top:340px"><svg viewBox="0 0 24 24"><path d="M14 6l-6 6 6 6V13h6v-2h-6z"/></svg></div>
<div class="abs arrow" style="left:1133px;top:340px"><svg viewBox="0 0 24 24"><path d="M10 6l6 6-6 6V13H4v-2h6z"/></svg></div>
<div class="abs hero-text">
  <div class="kicker">RELIABLE SERVICE FOR 100%</div>
  <h1>HARBOR LANE SERVICES W.L.L</h1>
  <p>Lorem Ipsum is simply dummy text of the printing and typesetting industry.</p>
</div>
<div class="abs btn-call">&#9654; Call Now!</div>

<div class="abs welcome"></div>
<div class="abs" style="left:161px;top:684px">
  <div class="heading">WELCOME TO</div>
  <div class="subhead">Harbor Lane Services</div>
</div>
<div class="abs body-copy" style="left:161px;top:757px;width:300px">
  <p>Lorem Ipsum is simply dummy text of the printing and typesetting industry. Lorem Ipsum has been the industry's standard dummy text ever since the 1500s...</p>
  <p style="margin-top:8px">Lorem Ipsum is simply dummy text of the printing and typesetting industry. Lorem Ipsum has been the industry's standard dummy text ever since the 1500s, when an unknown printer took a galley of type and scrambled it to make a type specimen book. It has survived not only five centuries, but also the leap into electronic typesetting, remaining essentially unchanged.</p>
</div>
<div class="abs btn-outline" style="left:161px;top:939px">Details</div>

<div class="abs why">WHY CHOOSE US?</div>

<div class="abs bubble b-green" style="left:498px;top:643px;width:192px;height:192px">
  <svg viewBox="0 0 36 36"><circle cx="18" cy="15" r="10"/><path d="M12 24l-3 9 5-2 3 4 1-7M24 24l3 9-5-2-3 4"/><path d="M14 15l3 3 5-6"/></svg>
  <h3>QUALITY</h3>
  <p>Lorem Ipsum is simply dummy text of the printing and typesetting industry. Lorem Ipsum has been...</p>
  <b>Read More!</b>
</div>
<div class="abs bubble b-dark" style="left:617px;top:782px;width:208px;height:208px">
  <svg viewBox="0 0 36 36"><circle cx="20" cy="5" r="3"/><path d="M20 9v10M14 14h12M10 20h14l-2 14H12z"/></svg>
  <h3>CLEANLINESS</h3>
  <p>Lorem Ipsum is simply dummy text of the printing and typesetting industry. Lorem Ipsum has been...</p>
  <b>Read More!</b>
</div>
<div class="abs bubble b-green" style="left:810px;top:820px;width:222px;height:222px">
  <svg viewBox="0 0 36 36"><path d="M2 14l7-6 6 3 6-3 7 6 6-2M9 8l-5 10 8 8 3-3M28 14l-10 10-2-2M24 18l-6 6M20 14l-5 3"/></svg>
  <h3>PROFESSIONALISM</h3>
  <p>Lorem Ipsum is simply dummy text of the printing and typesetting industry. Lorem Ipsum has been...</p>
  <b>Read More!</b>
</div>

<div class="abs services"></div>
<div class="abs rule" style="left:410px;top:1140px"></div>
<div class="abs rule" style="left:786px;top:1140px"></div>
<div class="abs services-title">
  <h2>Cleaning Services</h2>
  <p>Harbor Lane Services W.L.L</p>
</div>

<div class="abs card dark" style="left:161px">
  <div class="photo" role="img" aria-label="Photo of a bright modern living room being cleaned" style="background:linear-gradient(160deg,#f4f4f0,#dfe5d0 60%,#a7c24a)"></div>
  <div class="panel">
    <h3>JANITORIAL &nbsp;CLEANING</h3>
    <p>Lorem Ipsum is simply dummy text of the printing and typesetting industry. Lorem Ipsum has been the industry's standard dummy text ever since the 1500s, when an unknown printer took a galley of type and scrambled it to make...</p>
    <div class="more">&#9654; More Info</div>
  </div>
</div>
<div class="abs card light" style="left:461px">
  <div class="photo" role="img" aria-label="Photo of glass facade of a corporate building" style="background:linear-gradient(135deg,#8fb4d6,#dbe8f3 45%,#5b7fa4)"></div>
  <div class="panel">
    <h3>CORPORATE CLEANING</h3>
    <p>Lorem Ipsum is simply dummy text of the printing and typesetting industry. Lorem Ipsum has been the industry's standard dummy text ever since the 1500s, when an unknown printer took a galley of type and scrambled it to make...</p>
    <div class="more">&#9654; More Info</div>
  </div>
</div>
<div class="abs card dark" style="left:762px">
  <div class="photo" role="img" aria-label="Photo of a window being washed with spray and cloth" style="background:linear-gradient(135deg,#cfdbe6,#f2f5f8 50%,#9fb6cc)"></div>
  <div class="panel">
    <h3>BUILDINGS CLEANING</h3>
    <p>Lorem Ipsum is simply dummy text of the printing and typesetting industry. Lorem Ipsum has been the industry's standard dummy text ever since the 1500s, when an unknown printer took a galley of type and scrambled it to make...</p>
    <div class="more">&#9654; More Info</div>
  </div>
</div>

<div class="abs how"></div>
<div class="abs" style="left:161px;top:1712px">
  <div class="heading">HOW IT WORKS</div>
  <div class="subhead">Harbor Lane Services</div>
</div>
<div class="abs body-copy" style="left:161px;top:1786px;width:270px">Lorem Ipsum is simply dummy text of the printing and typesetting industry. Lorem Ipsum has been the industry's standard dummy text ever since the 1500s...</div>

<div class="abs step" style="left:443px">
  <div class="ring"><svg viewBox="0 0 36 36"><path d="M4 30L16 18M8 6l6 6-3 3-6-6M20 14h12v16H20zM23 19h6M23 23h6M23 27h4"/></svg></div>
  <p>Submit your<br><em>service request</em></p>
</div>
<div class="abs step" style="left:596px">
  <div class="ring"><svg viewBox="0 0 36 36"><circle cx="18" cy="15" r="10"/><path d="M13 15l4 4 6-7M12 24l-3 10 5-2 3 3M24 24l3 10-5-2-3 3"/></svg></div>
  <p>A certified<br><em>service<br>technician</em></p>
</div>
<div class="abs step" style="left:747px">
  <div class="ring"><svg viewBox="0 0 36 36"><rect x="5" y="8" width="26" height="23" rx="2"/><path d="M5 14h26M11 4v7M25 4v7M10 19h4M16 19h4M22 19h4M10 24h4M16 24h4M22 24h4"/></svg></div>
  <p>Reach out<br><em>to you shortly</em></p>
</div>
<div class="abs step" style="left:893px">
  <div class="ring"><svg viewBox="0 0 36 36"><circle cx="18" cy="18" r="13"/><path d="M18 9v9l6 4"/></svg></div>
  <p>Show Up<br><em>On Time</em></p>
</div>

<div class="abs strip"></div>
<div class="abs info" style="left:161px">
  <svg viewBox="0 0 52 48"><path d="M6 16c0-6 10-8 20-8s20 2 20 8l-6 3-4-6H16l-4 6zM14 22h24l6 20H8zM26 28a5 5 0 100 10 5 5 0 000-10z"/></svg>
  <div><h4>MAKE AN APPOINTMENT</h4><p>(000) 000-0000</p></div>
</div>
<div class="abs info" style="left:461px">
  <svg viewBox="0 0 52 48"><path d="M4 10h44v32H4zM4 10l22 18 22-18M4 42l16-16M48 42L32 26"/></svg>
  <div><h4>EMAIL</h4><p>info@harborlaneservices.com</p></div>
</div>
<div class="abs info" style="left:782px">
  <svg viewBox="0 0 52 48"><path d="M26 4a13 13 0 00-13 13c0 10 13 27 13 27s13-17 13-27A13 13 0 0026 4z"/><circle cx="26" cy="17" r="5"/></svg>
  <div><h4>VISIT US</h4><p class="small">Lorem Ipsum is simply dummy text of the printing and typesetting industry.</p></div>
</div>

<div class="abs contact" role="img" aria-label="Dark toned photo of a cleaning worker in a hallway"></div>
<h2 class="abs contact-title">CONTACT</h2>
<div class="abs field" style="top:2092px">&#128100;&nbsp;Name:</div>
<div class="abs field" style="top:2141px">&#9993;&nbsp;Email</div>
<div class="abs field" style="top:2191px">&#9743;&nbsp;Phone Number:</div>
<div class="abs field message" style="top:2240px">Message:</div>
<div class="abs submit">&#10150; Submit</div>
<div class="abs map" role="img" aria-label="Street map of the service area with a location pin marking the office"></div>

<div class="abs foot-left">Copyright © 2017 Harbor Lane Services W.L.L. All rights reserved.</div>
<div class="abs foot-right">Connect with us: <span class="social"></span><span class="social"></span><span class="social"></span></div>

</body>
</html>
```